Moulding supply company needs a Door Hanger Design

Door Hanger Design Request from Loft Crafta
www. loftcraftas.ca
We are moulding factory outlet in Toronto. Provide high quality moulding materials with competitive price like crown mouldings, casings, wainscoting, flatstocks, baseboards. We also provide professional installation for our clients. This door hanger will help the home owner easily find a local factory supplier with providing the materials as well as installation.

Detail request for design:
Size: 4”x11”, vertical
Shape: Rectangle

Content:
Front
1. Logo, see attachment(Use the left one, horizontal one)
2. Moulding factory outlet direct sale
3. Supply high quality Crown mouldings, baseboards, casings and wainscotings with competitive price
4. Installation & delivery
#2 content is the most important content, should be bold and readable
#3 can be smaller font compare to #2

Address: 47 West Falcon Ridge Rd, Richmond Hill, ON L3K 2P9
Telephone: 416 730 4215
416 682 1947
Email: info@loftcraftas.ca

Back
Slogan: Convert plain room into designer’s interiors

Telephone: 416 730 4215
416 682 1947
Email: info@loftcraftas.ca

Images:
Front
1. Display our productions for crown mouldings, baseboards, casings and wainscotings, refer to our website www.loftcraftas.ca. (The winner finally we will provide the high resolution images, low resolution please copy from our website so far)
Back
2. Display 4-6 nice images for 1. wainscoting walls 2. feature walls, 3. waffle ceiling like attached below. BUT PLEASE DON'T USE THE IMAGES PROVIDED, THIS IS ONLY A SAMPLE. Please use high resolution images for printing. ALSO PLEASE DON'T LIMIT YOUR CREATIVITY TO USE 4 SQUARES LIKE BELOW IMAGES. Please provide more ideas

Note:
1. Please do the bleeding for final printing production
2. Images have to be high resolution for ready to print
3. Style need to be fresh, clean, easy to read, modern and magazine style
4. Information has to be readable, easy to find, front and back both need to display company address, telephone, email, you can use icon or abbreviation to do these information.

Thanks,
Loft Craftas

```html
<!DOCTYPE html>
<html lang="en">
<head>
<meta charset="utf-8">
<title>Loft Craftas – Door Hangers</title>
<link href="https://fonts.googleapis.com/css2?family=Lato:wght@400;700;900&family=Oswald:wght@600;700&display=swap" rel="stylesheet">
<style>
  :root{
    --brand-blue:#2451a3;
    --brand-orange:#f05a28;
    --hole-ring:#262626;
    --hole-fill:#7c7c7c;
    --stage:#939393;
    --ink:#111;
    --white:#fff;
  }
  *{box-sizing:border-box;margin:0;padding:0}
  html,body{width:1200px;height:1200px;overflow:hidden;background:var(--stage)}
  .stage{position:relative;width:1200px;height:1200px}
  .hanger{position:absolute;top:146px;width:334px;height:920px;background:var(--white);overflow:hidden}
  .hanger--front{left:241px}
  .hanger--back{left:626px}
  .hanger__bg{position:absolute;inset:0}

  .brand-name{position:absolute;left:0;width:100%;display:flex;align-items:center;justify-content:center;gap:10px;color:var(--white);font-family:"Lato",sans-serif;font-weight:700;font-size:26px;line-height:1}
  .brand-name__square{width:18px;height:18px;background:var(--white)}

  .photo{position:absolute;border-radius:50%}

  .headline{position:absolute;left:0;width:100%;text-align:center;font-family:"Oswald",sans-serif;font-weight:700;text-transform:uppercase;line-height:1}
  .headline--blue{color:var(--brand-blue);font-size:36px;top:604px;letter-spacing:-.3px}
  .headline--orange{color:var(--brand-orange);font-size:36px;top:640px;letter-spacing:-.3px}

  .supply{position:absolute;left:25px;top:688px;width:300px;font-family:"Lato",sans-serif;font-weight:700;font-size:15.6px;line-height:19.5px;color:var(--ink)}
  .service-box{position:absolute;left:46px;top:761px;width:228px;height:32px;border:1.5px solid var(--brand-blue);color:var(--brand-orange);font-family:"Lato",sans-serif;font-weight:700;font-size:16px;display:flex;align-items:center;justify-content:center}

  .slogan{position:absolute;left:0;width:100%;text-align:center;color:var(--white)}
  .slogan__lead{top:284px;font-family:"Oswald",sans-serif;font-weight:700;font-size:21px;letter-spacing:-.2px;line-height:1}
  .slogan__big{font-family:"Lato",sans-serif;font-weight:900;font-size:46px;line-height:1;letter-spacing:-.5px}
  .slogan__big--one{top:308px}
  .slogan__big--two{top:352px}

  .feature{position:absolute;left:22px;display:flex;align-items:center;gap:14px}
  .feature__thumb{width:78px;height:78px;border-radius:50%;position:relative;flex:none}
  .feature__thumb svg{position:absolute;inset:0}
  .feature__label{font-family:"Oswald",sans-serif;font-weight:700;font-size:21px;color:var(--brand-orange);text-transform:uppercase;letter-spacing:-.2px}

  .contact-tab{position:absolute;top:806px;width:151px;height:26px;background:var(--brand-orange);border-radius:14px 14px 0 0;color:var(--white);font-family:"Lato",sans-serif;font-size:20px;display:flex;align-items:center;justify-content:center;padding-top:2px}
  .contact-list{position:absolute;left:44px;top:842px;color:var(--white);font-family:"Lato",sans-serif;font-weight:700;font-size:11.4px;line-height:11px;letter-spacing:-.1px}
  .contact-list__item{display:flex;align-items:flex-start;gap:6px;margin-bottom:10px}
  .contact-list__item svg{flex:none}
  .contact-list__sep{margin:0 6px}
</style>
</head>
<body>
<div class="stage">

  <section class="hanger hanger--front">
    <svg class="hanger__bg" width="334" height="920" viewBox="0 0 334 920">
      <polygon points="0,0 334,0 334,494 0,426" fill="var(--brand-blue)"/>
      <rect x="0" y="830" width="334" height="90" fill="var(--brand-blue)"/>
      <circle cx="169" cy="134" r="81" fill="var(--hole-ring)"/>
      <circle cx="169" cy="134" r="66" fill="var(--hole-fill)"/>
      <circle cx="161" cy="447" r="135" fill="var(--brand-orange)"/>
      <circle cx="164" cy="452" r="129" fill="var(--white)"/>
    </svg>

    <div class="brand-name" style="top:258px"><span class="brand-name__square"></span><span>LOFT CRAFTAS</span></div>

    <div class="photo" role="img" aria-label="Bright two-storey foyer with tall arched windows, chandelier and dark staircase railing"
         style="left:40px;top:328px;width:248px;height:248px;background:linear-gradient(160deg,#b9c3cc 0%,#8d99a4 45%,#4a4f55 100%)"></div>

    <div class="headline headline--blue">Moulding Factory</div>
    <div class="headline headline--orange">Outlet Direct Sale</div>

    <p class="supply">Supply High Quality Crown Mouldings, Baseboards, Casings and Wainscotings with Competitive Price</p>
    <div class="service-box">INSTALLATION &amp; DELIVERY</div>

    <div class="contact-tab" style="left:80px">Contact Us</div>
    <div class="contact-list">
      <div class="contact-list__item">
        <svg width="10" height="12" viewBox="0 0 10 12"><path d="M5 0a4.5 4.5 0 0 0-4.5 4.5C.5 8 5 12 5 12s4.5-4 4.5-7.5A4.5 4.5 0 0 0 5 0zm0 6.3a1.8 1.8 0 1 1 0-3.6 1.8 1.8 0 0 1 0 3.6z" fill="#fff"/></svg>
        <span>47 West Falcon Ridge Rd, Richmond Hill,<br>ON L3K 2P9</span>
      </div>
      <div class="contact-list__item">
        <svg width="10" height="10" viewBox="0 0 10 10"><circle cx="5" cy="5" r="4.3" fill="none" stroke="#fff" stroke-width=".9"/><path d="M3.3 2.8l1 1-.5.6c.3.7.9 1.3 1.6 1.6l.6-.5 1 1-.6.8C4.8 7.2 2.8 5.2 2.6 3.4z" fill="#fff"/></svg>
        <span>416 730 4215 | 416 682 1947</span>
      </div>
      <div class="contact-list__item">
        <svg width="10" height="10" viewBox="0 0 10 10"><rect x=".5" y="2" width="9" height="6" fill="#fff"/><path d="M.5 2l4.5 3.5L9.5 2" fill="none" stroke="var(--brand-blue)" stroke-width=".8"/></svg>
        <span>info@loftcraftas.ca<span class="contact-list__sep">|</span></span>
        <svg width="10" height="10" viewBox="0 0 10 10"><circle cx="5" cy="5" r="4.3" fill="none" stroke="#fff" stroke-width=".9"/><ellipse cx="5" cy="5" rx="1.8" ry="4.3" fill="none" stroke="#fff" stroke-width=".8"/><path d="M.7 5h8.6" stroke="#fff" stroke-width=".8"/></svg>
        <span>loftcraftas.ca</span>
      </div>
    </div>
  </section>

  <section class="hanger hanger--back">
    <svg class="hanger__bg" width="334" height="920" viewBox="0 0 334 920">
      <polygon points="0,0 334,0 334,462 0,392" fill="var(--brand-blue)"/>
      <polygon points="0,392 334,462 334,474 0,404" fill="var(--brand-orange)"/>
      <rect x="0" y="830" width="334" height="90" fill="var(--brand-blue)"/>
      <circle cx="170" cy="134" r="77" fill="var(--hole-ring)"/>
      <circle cx="170" cy="134" r="63" fill="var(--hole-fill)"/>
    </svg>

    <div class="brand-name" style="top:236px"><span class="brand-name__square"></span><span>LOFT CRAFTAS</span></div>

    <div class="slogan slogan__lead">CONVERT PLAIN ROOM INTO</div>
    <div class="slogan slogan__big slogan__big--one">DESIGNER’S</div>
    <div class="slogan slogan__big slogan__big--two">INTERIORS</div>

    <div class="feature" style="top:449px">
      <div class="feature__thumb">
        <svg width="78" height="78" viewBox="0 0 78 78"><circle cx="39" cy="39" r="35" fill="#dfe1e3" role="img" aria-label="White wainscoting moulding profile"/><path d="M2.5 39a36.5 36.5 0 0 1 73 0" fill="none" stroke="var(--brand-orange)" stroke-width="3"/><path d="M75.5 39a36.5 36.5 0 0 1-73 0" fill="none" stroke="var(--brand-blue)" stroke-width="3"/></svg>
      </div>
      <span class="feature__label">Wainscoting Walls</span>
    </div>
    <div class="feature" style="top:538px">
      <div class="feature__thumb">
        <svg width="78" height="78" viewBox="0 0 78 78"><circle cx="39" cy="39" r="35" fill="#e4e5e6" role="img" aria-label="Feature wall trim profile"/><path d="M2.5 39a36.5 36.5 0 0 1 73 0" fill="none" stroke="var(--brand-orange)" stroke-width="3"/><path d="M75.5 39a36.5 36.5 0 0 1-73 0" fill="none" stroke="var(--brand-blue)" stroke-width="3"/></svg>
      </div>
      <span class="feature__label">Feature Walls</span>
    </div>
    <div class="feature" style="top:627px">
      <div class="feature__thumb">
        <svg width="78" height="78" viewBox="0 0 78 78"><circle cx="39" cy="39" r="35" fill="#e2e3e4" role="img" aria-label="Flat stock board for waffle ceiling"/><path d="M2.5 39a36.5 36.5 0 0 1 73 0" fill="none" stroke="var(--brand-orange)" stroke-width="3"/><path d="M75.5 39a36.5 36.5 0 0 1-73 0" fill="none" stroke="var(--brand-blue)" stroke-width="3"/></svg>
      </div>
      <span class="feature__label">Waffle Ceiling</span>
    </div>
    <div class="feature" style="top:718px">
      <div class="feature__thumb">
        <svg width="78" height="78" viewBox="0 0 78 78"><circle cx="39" cy="39" r="35" fill="#e3e4e5" role="img" aria-label="White crown moulding profile"/><path d="M2.5 39a36.5 36.5 0 0 1 73 0" fill="none" stroke="var(--brand-orange)" stroke-width="3"/><path d="M75.5 39a36.5 36.5 0 0 1-73 0" fill="none" stroke="var(--brand-blue)" stroke-width="3"/></svg>
      </div>
      <span class="feature__label">Crown Mouldings</span>
    </div>

    <div class="contact-tab" style="left:81px">Contact Us</div>
    <div class="contact-list">
      <div class="contact-list__item">
        <svg width="10" height="12" viewBox="0 0 10 12"><path d="M5 0a4.5 4.5 0 0 0-4.5 4.5C.5 8 5 12 5 12s4.5-4 4.5-7.5A4.5 4.5 0 0 0 5 0zm0 6.3a1.8 1.8 0 1 1 0-3.6 1.8 1.8 0 0 1 0 3.6z" fill="#fff"/></svg>
        <span>47 West Falcon Ridge Rd, Richmond Hill,<br>ON L3K 2P9</span>
      </div>
      <div class="contact-list__item">
        <svg width="10" height="10" viewBox="0 0 10 10"><circle cx="5" cy="5" r="4.3" fill="none" stroke="#fff" stroke-width=".9"/><path d="M3.3 2.8l1 1-.5.6c.3.7.9 1.3 1.6 1.6l.6-.5 1 1-.6.8C4.8 7.2 2.8 5.2 2.6 3.4z" fill="#fff"/></svg>
        <span>416 730 4215 | 416 682 1947</span>
      </div>
      <div class="contact-list__item">
        <svg width="10" height="10" viewBox="0 0 10 10"><rect x=".5" y="2" width="9" height="6" fill="#fff"/><path d="M.5 2l4.5 3.5L9.5 2" fill="none" stroke="var(--brand-blue)" stroke-width=".8"/></svg>
        <span>info@loftcraftas.ca<span class="contact-list__sep">|</span></span>
        <svg width="10" height="10" viewBox="0 0 10 10"><circle cx="5" cy="5" r="4.3" fill="none" stroke="#fff" stroke-width=".9"/><ellipse cx="5" cy="5" rx="1.8" ry="4.3" fill="none" stroke="#fff" stroke-width=".8"/><path d="M.7 5h8.6" stroke="#fff" stroke-width=".8"/></svg>
        <span>loftcraftas.ca</span>
      </div>
    </div>
  </section>

</div>
</body>
</html>
```